Website Design - TallyPorchHelpers.net

PLEASE CHECK WORD DOCUMENT ATTACHED FOR WEBSITE FLOW.

Target Market(s)

REAL ESTATE AGENTS ARE THE TARGET MARKET

Industry/Entity Type

Real Estate

Coding

Coded - Design and coding required

Number of Pages Required

4 page

Colors

Designer to choose colors to be used in the design.

Requirements
Must have
• WE LIKE RED LOGO ATTACHED
Nice to have
• PLEASE CHECK WORD DOCUMENT ATTACHED FOR WEBSITE FLOW.
Should not have

```html
<!DOCTYPE html>
<html lang="en">
<head>
<meta charset="utf-8">
<title>TallyPorchHelpers.net</title>
<link href="https://fonts.googleapis.com/css2?family=Lato:wght@400;700;900&family=Oswald:wght@400&display=swap" rel="stylesheet">
<style>
:root{
  --red:#e4022d;
  --purple:#2c1b7c;
  --deep-purple:#3a1a74;
  --ink:#333333;
  --dark:#333333;
  --footer:#2f2f2f;
  --muted:#555555;
  --line:#cfcfcf;
  --white:#ffffff;
  --grad:linear-gradient(120deg,var(--red) 0%,var(--red) 30%,var(--purple) 100%);
}
*{box-sizing:border-box;margin:0;padding:0}
html,body{width:1200px;height:2308px;overflow:hidden}
body{font-family:"Lato",Arial,sans-serif;color:var(--ink);background:var(--white);position:relative}

/* header */
.site-header{position:absolute;left:0;top:0;width:1200px;height:118px;background:var(--white)}
.brand{position:absolute;left:74px;top:47px;font-weight:900;font-size:20px;color:var(--purple);display:flex;align-items:center;gap:8px;white-space:nowrap}
.brand-square{width:18px;height:18px;background:var(--purple)}
.main-nav{position:absolute;left:383px;top:56px;display:flex;gap:39px}
.main-nav a{font-size:13px;font-weight:700;color:var(--ink);text-decoration:none;letter-spacing:.3px}
.phone{position:absolute;left:928px;top:42px;display:flex;align-items:center;gap:17px}
.phone-badge{width:43px;height:43px;border-radius:50%;background:var(--red);display:flex;align-items:center;justify-content:center}
.phone-number{font-size:20px;font-weight:700;color:var(--red)}

/* hero */
.hero{position:absolute;left:0;top:118px;width:1200px;height:544px;background:linear-gradient(180deg,#3f4656 0%,#4a4f5c 40%,#3b4a35 80%,#4b5a3a 100%)}
.hero-text{position:absolute;left:100px;top:196px;width:1000px;text-align:center;color:var(--white);font-weight:900;font-size:31px;line-height:42px;text-shadow:0 2px 6px rgba(0,0,0,.45)}
.hero-arrow{position:absolute;top:222px}
.audience{position:absolute;top:600px;width:330px;height:123px;border-radius:6px;background:var(--grad);color:var(--white);text-align:center;font-weight:700;font-size:15px}
.audience svg{position:absolute;left:50%;top:26px;transform:translateX(-50%)}
.audience span{position:absolute;left:0;right:0;top:73px}

/* packages */
.packages{position:absolute;left:0;top:792px;width:1200px;height:603px;background:linear-gradient(180deg,#ececec 0%,#f7f7f7 35%,#ffffff 100%)}
.section-title{position:absolute;left:0;width:1200px;text-align:center;font-weight:700;font-size:28px}
.plan{position:absolute;top:125px;width:200px;height:415px;border:1px solid var(--line);border-radius:8px;background:var(--white);text-align:center;color:var(--ink)}
.plan-badge{position:absolute;left:54px;top:16px;width:92px;height:92px;border-radius:50%;background:var(--deep-purple);color:var(--white);font-family:"Oswald",sans-serif;font-size:21px;line-height:92px}
.plan-feature{position:absolute;left:6px;right:6px;font-size:14px;line-height:21px;white-space:nowrap}
.plan-feature.f1{top:123px}
.plan-feature.f2{top:222px}
.plan-feature.f3{top:281px}
.buy{position:absolute;left:27px;top:345px;width:145px;height:37px;border-radius:19px;background:var(--grad);color:var(--white);font-size:13px;font-weight:700;line-height:37px}
.plan.featured{background:linear-gradient(160deg,var(--red) 0%,var(--red) 25%,var(--purple) 90%);border-color:transparent;color:var(--white)}
.plan.featured .plan-badge{background:var(--white);color:var(--purple)}
.plan.featured .buy{background:var(--white);color:var(--red)}

/* services */
.services{position:absolute;left:0;top:1395px;width:1200px;height:394px;background:var(--dark);color:var(--white)}
.services .section-title{top:50px;color:var(--white);line-height:36px;font-size:29px}
.service{position:absolute;top:160px;width:246px;text-align:center}
.service svg{display:block;margin:0 auto}
.service h3{font-size:22px;font-weight:700;margin-top:14px;letter-spacing:.5px}
.service p{font-size:14px;line-height:21px;margin-top:9px;white-space:nowrap}

/* newsletter */
.newsletter{position:absolute;left:0;top:1789px;width:1200px;height:311px;background:var(--white)}
.newsletter .section-title{top:62px;font-size:29px}
.newsletter-lede{position:absolute;left:0;width:1200px;top:106px;text-align:center;font-size:18px;color:var(--muted)}
.signup{position:absolute;left:341px;top:157px;width:514px;height:43px;border:1px solid #bbb;border-radius:22px;overflow:hidden}
.signup input{position:absolute;left:0;top:0;width:411px;height:43px;border:0;padding-left:20px;font:14px "Lato",sans-serif;color:var(--ink);background:transparent}
.signup button{position:absolute;right:0;top:0;width:103px;height:43px;border:0;background:linear-gradient(90deg,var(--red),var(--purple));color:var(--white);font:700 15px "Lato",sans-serif}

/* footer */
.site-footer{position:absolute;left:0;top:2100px;width:1200px;height:208px;background:var(--footer);color:var(--white)}
.footer-brand{position:absolute;left:0;width:1200px;top:2080px;text-align:center;font-weight:900;font-size:22px;color:var(--red)}
.footer-nav{position:absolute;left:0;width:1200px;top:76px;display:flex;justify-content:center;gap:44px}
.footer-nav a{color:var(--white);font-size:13px;font-weight:700;text-decoration:none}
.copyright{position:absolute;left:0;width:1200px;top:109px;text-align:center;font-size:12px;color:#bdbdbd}
.social{position:absolute;left:0;width:1200px;top:146px;display:flex;justify-content:center;gap:22px}
.social span{width:18px;height:18px;border-radius:50%;background:var(--white)}
</style>
</head>
<body>

<header class="site-header">
  <div class="brand"><span class="brand-square"></span>TallyPorchHelpers.net</div>
  <nav class="main-nav">
    <a href="#">HOW IT WORKS</a><a href="#">SERVICE AREA</a><a href="#">PRICING</a><a href="#">ABOUT US</a><a href="#">FAQ</a>
  </nav>
  <div class="phone">
    <span class="phone-badge"><svg width="18" height="18" viewBox="0 0 24 24"><path fill="#fff" d="M6.6 10.8a15 15 0 0 0 6.6 6.6l2.2-2.2c.3-.3.7-.4 1-.2 1.1.4 2.3.6 3.6.6.6 0 1 .4 1 1V20c0 .6-.4 1-1 1A17 17 0 0 1 3 4c0-.6.4-1 1-1h3.5c.6 0 1 .4 1 1 0 1.3.2 2.5.6 3.6.1.3 0 .7-.2 1z"/></svg></span>
    <span class="phone-number">1-800-555-0142</span>
  </div>
</header>

<section class="hero" role="img" aria-label="Photo of a two-storey blue house with white trim and a stone porch among tall evergreen trees">
  <p class="hero-text">Helping agents save time and money. We place signs and boost<br>foot traffic to your&nbsp; open houses using proven<br>marketing techniques.</p>
  <svg class="hero-arrow" style="left:60px" width="22" height="32" viewBox="0 0 22 32"><path d="M17 4 6 16l11 12" fill="none" stroke="#fff" stroke-width="5"/></svg>
  <svg class="hero-arrow" style="left:1120px" width="22" height="32" viewBox="0 0 22 32"><path d="M5 4l11 12L5 28" fill="none" stroke="#fff" stroke-width="5"/></svg>
</section>

<a class="audience" style="left:75px">
  <svg width="26" height="30" viewBox="0 0 26 30"><circle cx="13" cy="8" r="7" fill="#fff"/><path d="M1 30c0-8 5-13 12-13s12 5 12 13z" fill="#fff"/></svg>
  <span>I'M A FULL ON BROKERAGE</span>
</a>
<a class="audience" style="left:434px">
  <svg width="36" height="28" viewBox="0 0 36 28"><circle cx="18" cy="7" r="6" fill="#fff"/><circle cx="7" cy="10" r="4.5" fill="#fff"/><circle cx="29" cy="10" r="4.5" fill="#fff"/><path d="M8 28c0-8 4-12 10-12s10 4 10 12z" fill="#fff"/><path d="M0 26c0-6 3-9 7-9 2 0 3 .5 4 1.5-2 2-3 5-3 7.5z" fill="#fff"/><path d="M36 26c0-6-3-9-7-9-2 0-3 .5-4 1.5 2 2 3 5 3 7.5z" fill="#fff"/></svg>
  <span>I'M AN IND. BROKER WITH A TEAM</span>
</a>
<a class="audience" style="left:797px">
  <svg width="28" height="28" viewBox="0 0 28 28"><rect x="1" y="1" width="26" height="26" rx="4" fill="#fff"/><path d="M8 20l1-4 9-9 3 3-9 9z" fill="var(--red)"/></svg>
  <span>I NEED SIGN PLACEMENT ASAP</span>
</a>

<section class="packages">
  <h2 class="section-title" style="top:60px">PACKAGES</h2>

  <article class="plan" style="left:75px">
    <div class="plan-badge">5 SIGNS</div>
    <p class="plan-feature f1">Place signs strategically<br>in best areas according to<br>where the open house<br>is located</p>
    <p class="plan-feature f2">Pick Up the signs after<br>the open house</p>
    <p class="plan-feature f3">Store custom signs for<br>you&nbsp; if needed</p>
    <div class="buy">BUY NOW</div>
  </article>
  <article class="plan" style="left:288px">
    <div class="plan-badge">10 SIGNS</div>
    <p class="plan-feature f1">Place signs strategically<br>in best areas according to<br>where the open house<br>is located</p>
    <p class="plan-feature f2">Pick Up the signs after<br>the open house</p>
    <p class="plan-feature f3">Store custom signs for<br>you&nbsp; if needed</p>
    <div class="buy">BUY NOW</div>
  </article>
  <article class="plan featured" style="left:500px">
    <div class="plan-badge">15 SIGNS</div>
    <p class="plan-feature f1">Place signs strategically<br>in best areas according to<br>where the open house<br>is located</p>
    <p class="plan-feature f2">Pick Up the signs after<br>the open house</p>
    <p class="plan-feature f3">Store custom signs for<br>you&nbsp; if needed</p>
    <div class="buy">BUY NOW</div>
  </article>
  <article class="plan" style="left:712px">
    <div class="plan-badge">20 SIGNS</div>
    <p class="plan-feature f1">Place signs strategically<br>in best areas according to<br>where the open house<br>is located</p>
    <p class="plan-feature f2">Pick Up the signs after<br>the open house</p>
    <p class="plan-feature f3">Store custom signs for<br>you&nbsp; if needed</p>
    <div class="buy">BUY NOW</div>
  </article>
  <article class="plan" style="left:925px">
    <div class="plan-badge">25 SIGNS</div>
    <p class="plan-feature f1">Place signs strategically<br>in best areas according to<br>where the open house<br>is located</p>
    <p class="plan-feature f2">Pick Up the signs after<br>the open house</p>
    <p class="plan-feature f3">Store custom signs for<br>you&nbsp; if needed</p>
    <div class="buy">BUY NOW</div>
  </article>
</section>

<section class="services">
  <h2 class="section-title">SERVICES-SIGN UP FOR A SUBSCRIPTION AND GET<br>THESE MARKETING SERVICES FOR FREE</h2>

  <div class="service" style="left:71px">
    <svg width="40" height="40" viewBox="0 0 40 40"><rect x="6" y="2" width="20" height="36" rx="3" fill="#fff"/><rect x="9" y="7" width="14" height="24" fill="var(--dark)"/><circle cx="29" cy="10" r="9" fill="#fff" stroke="var(--dark)" stroke-width="2"/><text x="29" y="13" font-size="7" font-weight="700" text-anchor="middle" fill="var(--dark)" font-family="Lato,sans-serif">SMS</text></svg>
    <h3>SMS</h3>
    <p>Send sms blast to your neighborhood<br>informing them your home is for sale<br>and if they know anyone looking to<br>send them over</p>
  </div>
  <div class="service" style="left:340px">
    <svg width="50" height="40" viewBox="0 0 50 40"><rect x="1" y="4" width="48" height="34" rx="3" fill="#fff"/><path d="M3 7l22 16L47 7" fill="none" stroke="var(--dark)" stroke-width="3"/></svg>
    <h3>EMAIL</h3>
    <p>Send email blast to your<br>neighborhood informing them your<br>home is for sale and if they know<br>anyone looking to send them over</p>
  </div>
  <div class="service" style="left:611px">
    <svg width="40" height="40" viewBox="0 0 40 40"><rect x="2" y="2" width="36" height="36" rx="5" fill="#fff"/></svg>
    <h3>SOCIAL AD</h3>
    <p>Newsfeed ads to people in your<br>open house area</p>
  </div>
  <div class="service" style="left:880px">
    <svg width="44" height="40" viewBox="0 0 44 40"><path d="M22 2 2 20h6v18h11V27h6v11h11V20h6z" fill="#fff"/></svg>
    <h3>VB</h3>
    <p>Send VB blast to your neighborhood<br>informing them your home is for sale<br>and if they know anyone looking to<br>send them over</p>
  </div>
</section>

<section class="newsletter">
  <h2 class="section-title">SIGN UP NEWSLETTER</h2>
  <p class="newsletter-lede">Mauris elementum vel quam et dignissim tristique nulla porttitor eget...</p>
  <form class="signup">
    <input type="email" placeholder="Enter Email Address">
    <button type="button">SIGN UP</button>
  </form>
</section>

<footer class="site-footer">
  <nav class="footer-nav">
    <a href="#">HOW IT WORKS</a><a href="#">SERVICE AREA</a><a href="#">PRICING</a><a href="#">ABOUT US</a><a href="#">FAQ</a>
  </nav>
  <p class="copyright">Copyright © 2018. Company Name.&nbsp; All Right Reserved</p>
  <div class="social"><span></span><span></span><span></span><span></span><span></span></div>
</footer>
<div class="footer-brand">TallyPorchHelpers.net</div>

</body>
</html>
```